Business Card Design

We are a commercial real estate brokerage in San Francisco, leasing office buildings downtown.
I would like a clean, elegant look. Simple but powerful .

Industry/Entity Type

Business

Contact Information for Business Card

Derek Holloway
lic# 07258143
415.555.0172
derek@velt-commercial.example
velt-commercial.example

```html
<!DOCTYPE html>
<html lang="en">
<head>
<meta charset="utf-8">
<title>VELT Commercial – Business Card</title>
<link rel="stylesheet" href="https://fonts.googleapis.com/css2?family=Source+Sans+3:wght@400;600;700&display=swap">
<style>
  :root {
    --slate: #7788a6;
    --ink: #1e1e1e;
    --mark-grey: #5a5a5a;
    --paper: #ffffff;
    --backdrop: #e9e7e4;
  }
  * { box-sizing: border-box; margin: 0; padding: 0; }
  html, body { width: 1200px; height: 900px; overflow: hidden; }
  body {
    background: var(--backdrop);
    font-family: "Source Sans 3", Arial, sans-serif;
    position: relative;
  }
  .card {
    position: absolute;
    background: var(--paper);
    border-radius: 18px;
    overflow: hidden;
    box-shadow: 0 6px 18px rgba(0,0,0,0.12);
  }

  /* Front */
  .card-front { left: 78px; top: 35px; width: 588px; height: 362px; }
  .front-band {
    position: absolute; left: 0; top: 27px; width: 100%; height: 103px;
    background: var(--slate);
  }
  .front-mark-plate {
    position: absolute; left: 101px; top: 27px; width: 141px; height: 103px;
    background: var(--paper);
    display: flex; align-items: center; justify-content: center;
  }
  .mark-square { width: 70px; height: 70px; background: var(--mark-grey); }
  .front-company {
    position: absolute; left: 268px; top: 40px;
    color: var(--paper); font-weight: 700;
    font-size: 38px; line-height: 1.02; letter-spacing: 1px;
  }
  .front-company span { display: block; font-size: 30px; letter-spacing: 0.5px; }
  .holder {
    position: absolute; left: 0; width: 100%; text-align: center;
  }
  .holder-name {
    top: 166px; color: var(--slate); font-weight: 600;
    font-size: 21px; letter-spacing: 0.5px;
  }
  .holder-licence { top: 220px; font-size: 16px; color: var(--ink); font-weight: 600; }
  .holder-licence .label { color: var(--slate); }
  .contact-list { top: 266px; font-size: 16px; color: var(--ink); line-height: 25px; list-style: none; }
  .contact-list li { display: flex; align-items: center; justify-content: center; gap: 5px; }
  .contact-list svg { width: 11px; height: 11px; fill: var(--slate); }

  /* Back */
  .card-back { left: 390px; top: 506px; width: 564px; height: 350px; }
  .back-stripe {
    position: absolute; left: 38px; top: 0; width: 44px; height: 100%;
    background: var(--slate);
  }
  .back-lockup {
    position: absolute; left: 136px; top: 130px;
    display: flex; align-items: center; gap: 12px;
  }
  .back-lockup .mark-square { width: 76px; height: 76px; }
  .lockup-rule { width: 2px; height: 90px; background: var(--ink); }
  .back-company {
    color: var(--slate); font-weight: 700; font-size: 44px; line-height: 1; letter-spacing: 1px;
  }
  .back-company span { display: block; font-size: 24px; letter-spacing: 0.5px; }
</style>
</head>
<body>

<section class="card card-front" aria-label="Business card front">
  <div class="front-band"></div>
  <div class="front-mark-plate"><div class="mark-square"></div></div>
  <div class="front-company">VELT<span>COMMERCIAL</span></div>

  <p class="holder holder-name">DEREK HOLLOWAY</p>
  <p class="holder holder-licence"><span class="label">Lic#</span> 07258143</p>
  <ul class="holder contact-list">
    <li>
      <svg viewBox="0 0 24 24"><path d="M6.6 10.8a15 15 0 0 0 6.6 6.6l2.2-2.2a1 1 0 0 1 1-.25 11.4 11.4 0 0 0 3.6.57 1 1 0 0 1 1 1V20a1 1 0 0 1-1 1A17 17 0 0 1 3 4a1 1 0 0 1 1-1h3.5a1 1 0 0 1 1 1c0 1.25.2 2.45.57 3.57a1 1 0 0 1-.25 1z"/></svg>
      415.555.0172
    </li>
    <li>
      <svg viewBox="0 0 24 24"><path d="M2 5h20v14H2z M2 5l10 8 10-8" fill="none" stroke="#7788a6" stroke-width="2.5"/><path d="M2 5h20l-10 8z"/></svg>
      derek@velt-commercial.example
    </li>
    <li>
      <svg viewBox="0 0 24 24"><path d="M10 14a4 4 0 0 1 0-5.7l3-3a4 4 0 0 1 5.7 5.7l-1.5 1.5M14 10a4 4 0 0 1 0 5.7l-3 3a4 4 0 0 1-5.7-5.7l1.5-1.5" fill="none" stroke="#7788a6" stroke-width="2.5" stroke-linecap="round"/></svg>
      velt-commercial.example
    </li>
  </ul>
</section>

<section class="card card-back" aria-label="Business card back">
  <div class="back-stripe"></div>
  <div class="back-lockup">
    <div class="mark-square"></div>
    <div class="lockup-rule"></div>
    <div class="back-company">VELT<span>COMMERCIAL</span></div>
  </div>
</section>

</body>
</html>
```